Local fast-growing company in the service sector

We are looking for a modern business card design, which should also appear on our letterheads

Target Market(s)

Private and industrial sectors

Contact Information for Business Card

Vorname Name
Kellberger Str. 18
71548 Tannfeld
Tel.: 07146-839214-0
Name@agentur-kvtl.de

Colors
9d9d9d
919191
aaaaaa

Requirements
Must have
• The logo (file) in silver

```html
<!DOCTYPE html>
<html lang="de">
<head>
<meta charset="utf-8">
<title>KVTL Visitenkarte</title>
<link rel="stylesheet" href="https://fonts.googleapis.com/css2?family=Montserrat:wght@400;700&display=swap">
<style>
  :root {
    --page-bg: #e4e4e4;
    --card-dark: #232323;
    --card-mid: #353535;
    --silver: #aaaaaa;
    --silver-light: #c4c4c4;
    --text-soft: #d2d2d2;
  }
  html, body {
    margin: 0;
    padding: 0;
    overflow: hidden;
  }
  .canvas {
    position: relative;
    width: 1200px;
    height: 576px;
    background: var(--page-bg);
    overflow: hidden;
    font-family: "Montserrat", sans-serif;
  }
  .card {
    position: absolute;
    top: 138px;
    border-radius: 13px;
    background: radial-gradient(ellipse at 50% 45%, var(--card-mid) 0%, var(--card-dark) 75%);
    overflow: hidden;
  }
  .card--front {
    left: 82px;
    width: 485px;
    height: 294px;
  }
  .card--back {
    left: 602px;
    width: 480px;
    height: 292px;
  }
  .brand {
    position: absolute;
    display: flex;
    align-items: center;
    color: var(--silver);
    font-weight: 700;
    letter-spacing: 0.02em;
    line-height: 1;
  }
  .brand__mark {
    background: var(--silver);
  }
  .card--front .brand {
    left: 0;
    right: 0;
    top: 0;
    bottom: 0;
    justify-content: center;
    font-size: 76px;
    gap: 20px;
  }
  .card--front .brand__mark {
    width: 62px;
    height: 62px;
  }
  .card--back .brand {
    right: 24px;
    bottom: 26px;
    font-size: 50px;
    gap: 12px;
  }
  .card--back .brand__mark {
    width: 42px;
    height: 42px;
  }
  .person-name {
    position: absolute;
    left: 23px;
    top: 35px;
    margin: 0;
    font-size: 20px;
    font-weight: 700;
    letter-spacing: 0.1em;
    color: var(--silver-light);
  }
  .address {
    position: absolute;
    left: 23px;
    top: 174px;
    margin: 0;
    font-style: normal;
    font-size: 12.5px;
    line-height: 17px;
    color: var(--text-soft);
  }
  .contact-list {
    position: absolute;
    left: 23px;
    top: 216px;
    margin: 0;
    padding: 0;
    list-style: none;
    font-size: 12.5px;
    line-height: 17px;
    color: var(--text-soft);
  }
  .contact-list li {
    display: flex;
    align-items: center;
    gap: 11px;
  }
  .contact-list svg {
    width: 9px;
    height: 9px;
    fill: var(--text-soft);
    stroke: var(--text-soft);
  }
</style>
</head>
<body>
<div class="canvas">
  <section class="card card--front" aria-label="Vorderseite">
    <div class="brand"><span class="brand__mark"></span><span>KVTL</span></div>
  </section>

  <section class="card card--back" aria-label="Rückseite">
    <h1 class="person-name">VORNAME NAME</h1>
    <address class="address">
      Kellberger Str. 18<br>
      71548 Tannfeld
    </address>
    <ul class="contact-list">
      <li>
        <svg viewBox="0 0 10 10" aria-hidden="true"><path stroke="none" d="M1 3.5 C1 1.5 9 1.5 9 3.5 L7.5 4.5 L6.5 3.5 L3.5 3.5 L2.5 4.5 Z M2.5 5 L7.5 5 L8.5 8.5 L1.5 8.5 Z"/></svg>
        <span>07146-839214-0</span>
      </li>
      <li>
        <svg viewBox="0 0 10 10" aria-hidden="true"><rect x="0.5" y="2" width="9" height="6" stroke="none"/><path d="M0.8 2.3 L5 5.5 L9.2 2.3" fill="none" stroke="#2a2a2a" stroke-width="0.9"/></svg>
        <span>Name@agentur-kvtl.de</span>
      </li>
      <li>
        <svg viewBox="0 0 10 10" aria-hidden="true"><circle cx="5" cy="5" r="4.2" fill="none" stroke-width="1"/><path d="M0.8 5 H9.2 M5 0.8 C2.5 3 2.5 7 5 9.2 M5 0.8 C7.5 3 7.5 7 5 9.2" fill="none" stroke-width="0.8"/></svg>
        <span>www.agentur-kvtl.de</span>
      </li>
    </ul>
    <div class="brand"><span class="brand__mark"></span><span>KVTL</span></div>
  </section>
</div>
</body>
</html>
```